Business Card front and back

I am looking for business card design. I really really like the design file I uploaded named 627788_19250069_3478263_85f427ee_image

Target Market(s)

Corporate Fitness High end Private country club

Industry/Entity Type

Fitness Industry

Contact Information for Business Card

The last image I like as an example I uploaded a bunch of my logos. The file labeled "the signature" is my business card information for you to use

Colors
0054AA
0677BA
7BADD7
CADEEF
E8F1F8

Requirements
Must have
• E-mail sigThe file I uploaded labeled "627788_19250069_3478263_85f427ee_image" with all the plus signs on the back if those could be the logo symbol I uploaded labeled "1 back.png"

```html
<!DOCTYPE html>
<html lang="en">
<head>
<meta charset="utf-8">
<title>Forma Athletic – Business Card</title>
<link href="https://fonts.googleapis.com/css2?family=Lato:wght@400;700;900&display=swap" rel="stylesheet">
<style>
  :root {
    --page-bg: #1e1e1f;
    --card-dark: #303031;
    --silver: #b9b9bb;
    --brand-blue: #457dc2;
    --panel-white: #ffffff;
    --panel-grey: #e1e1e1;
    --ink-dark: #2a2a2c;
    --text-light: #ffffff;
  }
  * { box-sizing: border-box; margin: 0; padding: 0; }
  html, body { width: 1200px; height: 1122px; overflow: hidden; }
  body {
    background: var(--page-bg);
    font-family: "Lato", sans-serif;
    position: relative;
  }
  .card {
    position: absolute;
    width: 760px;
    height: 434px;
    border-radius: 30px;
    overflow: hidden;
  }
  /* Back of card */
  .card-back {
    left: 330px;
    top: 70px;
    background: var(--card-dark);
    display: flex;
    align-items: center;
    justify-content: center;
  }
  .card-back .brand-name {
    font-weight: 900;
    font-size: 58px;
    letter-spacing: 4px;
    color: var(--silver);
    text-transform: uppercase;
  }
  /* Front of card */
  .card-front {
    left: 110px;
    top: 610px;
    background: var(--brand-blue);
  }
  .brand-panel {
    position: absolute;
    left: 0;
    top: 80px;
    width: 420px;
    height: 270px;
    background: var(--panel-white);
    border-radius: 0 34px 34px 0;
  }
  .brand-panel .band {
    position: absolute;
    left: 0;
    top: 50px;
    width: 360px;
    height: 110px;
    background: var(--panel-grey);
  }
  .brand-panel .brand-name {
    position: absolute;
    left: 36px;
    top: 87px;
    font-weight: 900;
    font-size: 30px;
    line-height: 36px;
    letter-spacing: 2px;
    color: var(--ink-dark);
    text-transform: uppercase;
    white-space: nowrap;
  }
  .contact {
    position: absolute;
    right: 48px;
    top: 122px;
    text-align: right;
    color: var(--text-light);
  }
  .contact .person-name {
    font-weight: 900;
    font-size: 40px;
    letter-spacing: 1px;
    line-height: 1;
  }
  .contact .person-role {
    font-weight: 400;
    font-size: 24px;
    margin-top: 4px;
    margin-bottom: 14px;
  }
  .contact .line {
    display: flex;
    justify-content: flex-end;
    align-items: center;
    gap: 10px;
    font-size: 20px;
    line-height: 30px;
  }
  .contact .line svg { width: 18px; height: 18px; }
  .contact .regions {
    font-size: 20px;
    letter-spacing: 1px;
    margin-top: 14px;
    padding-right: 28px;
  }
</style>
</head>
<body>
  <section class="card card-back" aria-label="Card back">
    <div class="brand-name">Forma Athletic</div>
  </section>

  <section class="card card-front" aria-label="Card front">
    <div class="brand-panel">
      <div class="band"></div>
      <div class="brand-name">Forma Athletic</div>
    </div>

    <div class="contact">
      <div class="person-name">SAM ORTEGA</div>
      <div class="person-role">Consultant</div>
      <div class="line">555-014-2286
        <svg viewBox="0 0 24 24" aria-hidden="true"><path fill="#fff" d="M6.6 10.8a15.1 15.1 0 0 0 6.6 6.6l2.2-2.2a1 1 0 0 1 1-.25 11.4 11.4 0 0 0 3.6.57 1 1 0 0 1 1 1V20a1 1 0 0 1-1 1A17 17 0 0 1 3 4a1 1 0 0 1 1-1h3.5a1 1 0 0 1 1 1c0 1.250.2 2.45.57 3.57a1 1 0 0 1-.25 1z"/></svg>
      </div>
      <div class="line">sam@formaathletic.co
        <svg viewBox="0 0 24 24" aria-hidden="true"><rect x="2" y="5" width="20" height="14" rx="1.5" fill="none" stroke="#fff" stroke-width="2"/><path d="M2 6l10 7 10-7" fill="none" stroke="#fff" stroke-width="2"/></svg>
      </div>
      <div class="line">formaathletic.co
        <svg viewBox="0 0 24 24" aria-hidden="true"><circle cx="12" cy="12" r="9.5" fill="none" stroke="#fff" stroke-width="2"/><path d="M2.5 12h19M12 2.5c3 3 3 16 0 19M12 2.5c-3 3-3 16 0 19" fill="none" stroke="#fff" stroke-width="1.6"/></svg>
      </div>
      <div class="regions">Serving Six Regions</div>
    </div>
  </section>
</body>
</html>
```